Bold and colurful E-liquid Design Template

I'm looking for a new label for my house range of vape e-liquids. I currently have almost 40 flavours, so I'm looking for a single label design that I can modify to create the rest of the flavours.
Each label will have the same design, but I'll change the color for each flavour and the name.
I'd like the label to be predominantly text based with bold text and bold colours. I like bold typographic styles. Also for each flavour I'd like to add 1 - 3 letters to represent the flavour. This can be in a larger font.
eg for
Blueberry I'll use the letter B
Pineapple Peach will use PP
Cinnamon Blueberry Muffin uses CBM
The colour used on the label will also be important so they stand out nicely on the shelf.
I've attached a psd mockup of the bottles I'll be using.

```html
<!DOCTYPE html>
<html lang="en">
<head>
<meta charset="utf-8">
<title>Moonfox Blueberry E-Liquid Label</title>
<link rel="stylesheet" href="https://fonts.googleapis.com/css2?family=Montserrat:wght@400;500;700;900&display=swap">
<style>
  :root {
    --backdrop: #e4e5e6;
    --label-white: #fbfbfd;
    --flavour-light: #8a6cb3;
    --flavour: #4b2a86;
    --flavour-dark: #2a0b62;
    --ink: #141414;
    --brand-box: #0d0d0d;
  }
  * { margin: 0; padding: 0; box-sizing: border-box; }
  html, body {
    width: 975px;
    height: 1200px;
    overflow: hidden;
    background: var(--backdrop);
  }
  .canvas {
    position: relative;
    width: 975px;
    height: 1200px;
  }
  .label {
    position: absolute;
    left: 267px;
    top: 15px;
    width: 440px;
    height: 1170px;
    background: var(--label-white);
    font-family: "Montserrat", sans-serif;
    color: var(--ink);
    overflow: hidden;
  }
  .label__burst {
    position: absolute;
    left: 0;
    top: 200px;
    width: 440px;
    height: 880px;
    background: radial-gradient(ellipse at 50% 47%, #f1e6f8 0%, #f6f0fa 35%, rgba(251,251,253,0) 72%);
  }
  .band {
    position: absolute;
    left: 0;
    width: 100%;
    height: 40px;
    background: var(--flavour-dark);
  }
  .band::after {
    content: "";
    position: absolute;
    left: 0;
    right: 0;
    height: 3px;
    background: var(--flavour-light);
  }
  .band--top { top: 0; }
  .band--top::after { bottom: 6px; }
  .band--bottom { bottom: 5px; }
  .band--bottom::after { top: 6px; }

  .brand {
    position: absolute;
    left: 50%;
    top: 95px;
    transform: translateX(-50%);
    width: 270px;
    height: 92px;
    background: var(--brand-box);
    color: #ffffff;
    font-weight: 400;
    font-size: 44px;
    letter-spacing: 1px;
    line-height: 92px;
    text-align: center;
    white-space: nowrap;
  }
  .flavour-code {
    position: absolute;
    left: 0;
    width: 100%;
    top: 270px;
    text-align: center;
    font-weight: 900;
    font-size: 250px;
    line-height: 250px;
    color: var(--flavour);
  }
  .flavour-name {
    position: absolute;
    left: 0;
    width: 100%;
    top: 530px;
    text-align: center;
    font-weight: 900;
    font-size: 64px;
    line-height: 80px;
    letter-spacing: -1px;
    white-space: nowrap;
    color: var(--ink);
  }
  .product-type {
    position: absolute;
    left: 50%;
    top: 705px;
    transform: translateX(-50%);
    width: 330px;
    height: 120px;
    background: var(--flavour);
    color: #ffffff;
    font-weight: 700;
    font-size: 56px;
    letter-spacing: 3px;
    line-height: 120px;
    text-align: center;
    white-space: nowrap;
  }
  .strength {
    position: absolute;
    left: 0;
    width: 100%;
    top: 870px;
    text-align: center;
    font-weight: 500;
    font-size: 40px;
    line-height: 50px;
    white-space: nowrap;
  }
  .divider {
    position: absolute;
    left: 50%;
    top: 968px;
    transform: translateX(-50%);
    width: 312px;
    height: 4px;
    background: var(--flavour-dark);
  }
  .volume {
    position: absolute;
    left: 0;
    width: 100%;
    top: 1030px;
    text-align: center;
    font-weight: 700;
    font-size: 54px;
    line-height: 64px;
  }
</style>
</head>
<body>
  <main class="canvas">
    <section class="label">
      <div class="label__burst" role="img" aria-label="Soft lilac sunburst rays radiating from behind the flavour name"></div>
      <div class="band band--top"></div>
      <div class="brand">MOONFOX</div>
      <div class="flavour-code">B</div>
      <h1 class="flavour-name">BLUEBERRY</h1>
      <div class="product-type">E-LIQUID</div>
      <p class="strength">70mg / 30ml</p>
      <div class="divider"></div>
      <p class="volume">60ml</p>
      <div class="band band--bottom"></div>
    </section>
  </main>
</body>
</html>
```